Home Page Design (+50 More Pages To Winning Designer!)

We have a 50+ page website, but we're starting with the home page. The winning designer will get all 50+ pages to design as a 2nd project, so make sure you do your best!

Velorane is in the private jet industry and needs a re-designed website.

We have created the structure for the website and content inside of Frandle.io (THESE ARE ONLY ROUGH A.I. GENERATED WIREFRAMES AND DO NOT NEED TO BE FOLLOWED EXACTLY) - https://www.frandle.io/app/project/K482915_qWmRtZaLs-KDnHoUvvy82QJ5cfhaR61trkwqlDV3Hm

Take the content from the 'Home Page' under the 'Wireframe' tab on the Frandle.io link above, but feel free to re-design the page in a better way as these are only A.I. generated wireframes.

We want a DARK theme.... High quality, luxurious feel, greyscale colors. Attached is a brand guideline (BUT THIS IS NOT A 100% BRAND GUIDELINE, YOU CAN CHANGE COLORS AND FONTS AND MAKE CHANGES IF YOU HAVE BETTER IDEAS) and attached is our logo. We are also attaching some examples of other apps and websites to give you a guideline of what we're looking for for this design project.

The final design MUST communicate luxury using high-quality imagery of large cabin luxurious private jets.
Updates

ENTRIES THAT DO NOT FOLLOW THE PROJECT BRIEF WILL BE AUTOMATICALLY DISCARDED. FOLLOW THE INSTRUCTIONS!

Industry/Entity Type

Travel

Number of Pages Required

1 page

Font styles to use
Sans Serif

Colors

Designer to choose colors to be used in the design.

Requirements
Must have
• Follow wireframe and use content in wireframe (see Frandle.io link)

```html
<!DOCTYPE html>
<html lang="en">
<head>
<meta charset="utf-8">
<title>Velorane — Home Page</title>
<link href="https://fonts.googleapis.com/css2?family=Plus+Jakarta+Sans:ital,wght@0,300;0,400;0,500;0,600;0,700;0,800;1,700;1,800&family=Montserrat:wght@400;500&display=swap" rel="stylesheet">
<style>
:root{
  --board:#1e2327;
  --page:#0b0b0b;
  --panel:#161616;
  --card:#1c1c1c;
  --line:#2e2e2e;
  --ink:#ffffff;
  --muted:#a9a9a9;
  --gold:#d5b46a;
  --gold-light:#f3e3a6;
  --gold-deep:#9c7a35;
}
*{box-sizing:border-box;margin:0;padding:0}
html,body{width:1200px;height:1200px;overflow:hidden;background:var(--board)}
body{position:relative;font-family:"Plus Jakarta Sans",sans-serif;color:var(--ink)}
.abs{position:absolute}
.board-label{position:absolute;font-family:"Montserrat",sans-serif;font-weight:500;color:#fff;white-space:nowrap;transform:translate(-50%,-50%) rotate(-90deg)}
.board-label.home{left:81px;top:600px;font-size:46px;letter-spacing:2px}
.board-label.thanks{left:1121px;top:600px;font-size:26px;letter-spacing:3px}

.page{position:absolute;background:var(--page);overflow:hidden}
.page.left{left:145px;top:52px;width:408px;height:1148px;
  background:linear-gradient(180deg,#0a0a0a 0%,#141210 30%,#0c0c0c 45%,#0a0a0a 60%,#15130f 80%,#0b0b0b 100%)}
.page.right{left:638px;top:0;width:408px;height:1178px}

.watermark{position:absolute;font-weight:800;color:rgba(255,255,255,.035);letter-spacing:2px;white-space:nowrap;line-height:1}

.logo{font-weight:400;font-size:13px;letter-spacing:-.2px;display:flex;align-items:center;gap:3px}
.logo .mark{width:8px;height:8px;background:#fff;border-radius:2px}
.nav a{position:absolute;font-size:3.3px;color:#ddd;text-decoration:none}
.btn{position:absolute;display:flex;align-items:center;justify-content:center;font-size:2.8px;font-weight:700;text-transform:uppercase;letter-spacing:.2px;border-radius:8px;height:13px}
.btn.outline{border:.6px solid #e5e5e5;color:#fff}
.btn.gold{background:linear-gradient(90deg,var(--gold-deep),var(--gold-light));color:#1a1a1a;border-radius:6px}
.btn.dark{background:#111;color:#fff}
.learn{position:absolute;font-size:3.2px;color:var(--gold);display:flex;align-items:center;gap:3px}
.learn i{display:block;width:6px;height:.6px;background:#ddd;position:relative}
.learn i::after{content:"";position:absolute;right:0;top:-1px;width:1.6px;height:1.6px;border-top:.6px solid #ddd;border-right:.6px solid #ddd;transform:rotate(45deg)}

.eyebrow{position:absolute;font-size:4px;letter-spacing:.6px;color:var(--gold);text-transform:uppercase;font-weight:500}
.h-section{position:absolute;font-size:12.4px;font-weight:400;line-height:15.3px}
.h-section em,.h-hero em,.h-cta em{font-style:italic;font-weight:800;text-transform:uppercase}
.h-hero{position:absolute;font-size:21px;font-weight:300;line-height:23px}
.h-hero em{font-size:25px;display:block;margin-top:2px}
.h-cta{position:absolute;font-size:15.5px;font-weight:300;line-height:15.5px}
.h-cta em{font-size:17px;display:block;margin-top:1px}
.body{position:absolute;font-size:3.3px;line-height:6.8px;color:#cfcfcf}
.body b{color:#fff}

.photo{position:absolute;overflow:hidden}
.rule{position:absolute;height:.5px;background:var(--line)}

.feature{position:absolute;left:253px;width:108px;font-size:3.4px;font-weight:500;display:flex;align-items:center;gap:4px;padding-bottom:5px;border-bottom:.5px solid var(--line)}
.feature .dot{width:4px;height:4px;border-radius:1px;background:#fff}

.program{position:absolute;left:48px;width:149px;height:39px;border:.5px solid #2c2c2c;border-radius:4px;padding:9px 13px;background:#171717}
.program.active{background:linear-gradient(100deg,#242424,#1f1f1f)}
.program h4{font-size:5px;font-weight:600;margin-bottom:5px}
.program p{font-size:3px;line-height:5.5px;color:#bdbdbd}

.benefit{position:absolute;left:222px;width:148px;height:38px;border:.5px solid #303030;border-radius:5px;background:#1b1b1b;display:flex;align-items:center;gap:8px;padding:0 6px}
.benefit .tick{width:20px;height:20px;border-radius:50%;border:.6px solid #777;display:flex;align-items:center;justify-content:center;flex:none}
.benefit h4{font-size:5px;font-weight:500;margin-bottom:4px}
.benefit p{font-size:3px;line-height:5.3px;color:#bdbdbd}

.service{position:absolute;width:98px;background:#1a1a1a;border-radius:4px 10px 0 0;padding:10px 9px}
.service h4{font-size:5px;font-weight:500;line-height:6px;margin-top:13px}
.service .bar{width:21px;height:.5px;background:#888;margin:6px 0 6px}
.service p{font-size:3px;color:#bbb;line-height:5px}

.testimonial{position:absolute;width:119px;height:69px;background:#1e1e1e;border:.5px solid #2a2a2a;border-radius:3px;padding:9px}
.testimonial .quote{font-size:14px;font-weight:800;line-height:9px;color:#ddd}
.testimonial .stars{font-size:5px;color:var(--gold);letter-spacing:.5px;margin:3px 0 4px}
.testimonial p{font-size:3.6px;font-style:italic;line-height:5.6px;color:#ddd}
.author{position:absolute;display:flex;align-items:center;gap:4px;font-size:3.4px;font-weight:700}
.author .avatar{width:15px;height:15px;border-radius:50%;background:linear-gradient(135deg,#9a9a9a,#444)}
.author small{display:block;font-size:2.4px;font-weight:400;color:#aaa}
.brand{display:inline-flex;align-items:center;gap:2px;font-size:4.2px;font-weight:600;color:#ddd}
.brand .sq{width:3.4px;height:3.4px;background:#ddd;border-radius:.5px}
.brand .ci{width:3.6px;height:3.6px;background:#ddd;border-radius:50%}

.faq-q{position:absolute;left:48px;width:312px;font-size:4.4px;font-weight:500;display:flex;justify-content:space-between}
.faq-q span:last-child{font-size:6px;line-height:4px}

.foot-col{position:absolute;top:1080px}
.foot-col h5{font-size:4.4px;font-weight:600;margin-bottom:5px}
.foot-col a{display:block;font-size:3px;color:#bbb;margin-bottom:4.9px;text-decoration:none}
.social{position:absolute;top:1160px;width:10px;height:10px;border-radius:50%;border:.5px solid #555;display:flex;align-items:center;justify-content:center}
.social i{width:3px;height:3px;background:#ddd;border-radius:50%}
</style>
</head>
<body>

<div class="board-label home">HOME PAGE</div>
<div class="board-label thanks">THANK YOU FOR WATCHING</div>

<!-- ===== Home page: upper half ===== -->
<main class="page left">
  <div class="watermark" style="left:22px;top:38px;font-size:62px">VELORANE</div>
  <div class="watermark" style="left:48px;top:760px;font-size:58px">VELORANE</div>

  <header>
    <div class="logo abs" style="left:22px;top:11px"><span>Velorane</span><span class="mark"></span></div>
    <nav class="nav">
      <a style="left:153px;top:16px">Aircraft</a>
      <a style="left:177px;top:16px">Programs</a>
      <a style="left:206px;top:16px">Why Velorane</a>
      <a style="left:240px;top:16px">Lifestyle</a>
    </nav>
    <div class="abs" style="left:328px;top:13px;width:10px;height:10px;border-radius:50%;border:.5px solid #888"></div>
    <div class="btn gold" style="left:342px;top:12px;width:42px;height:11px">Contact Us</div>
  </header>

  <section class="hero">
    <h1 class="h-hero" style="left:48px;top:100px">Experience The<br>Ultimate In Luxury<em>Jet Travel</em></h1>
    <p class="body" style="left:48px;top:176px;width:160px">Velorane offers fractional jet ownership, jet card program, private jet lease program, all access program, helicopter access programs, and by the seat charter flights. discover the perfect flight program for your needs.</p>
    <div class="btn outline" style="left:48px;top:210px;width:46px">Explore Now</div>
    <div class="learn" style="left:102px;top:215px">Learn More <i></i></div>
    <div class="photo" role="img" aria-label="Traveller seated in a leather jet cabin seat" style="left:260px;top:56px;width:124px;height:119px;border-radius:0 62px 0 0;background:linear-gradient(135deg,#7a5a3c,#3a2a1e 55%,#151210)"></div>
    <div class="photo" role="img" aria-label="Monochrome private jet cabin interior" style="left:240px;top:137px;width:88px;height:88px;border-radius:0 0 0 44px;background:linear-gradient(135deg,#b9b9b9,#6a6a6a 60%,#2a2a2a)"></div>
  </section>

  <div class="rule" style="left:48px;top:256px;width:250px"></div>

  <section class="aircraft">
    <div class="photo" role="img" aria-label="Private jet parked on the apron in black and white" style="left:296px;top:238px;width:88px;height:89px;border-radius:0 44px 0 0;background:linear-gradient(160deg,#e6e6e6,#8a8a8a 55%,#3c3c3c)"></div>
    <div class="eyebrow" style="left:48px;top:287px">Discover our aircraft</div>
    <h2 class="h-section" style="left:48px;top:295px">Experience The Luxury<br>of Fractional <em>Jet Ownership</em></h2>
    <div class="photo" role="img" aria-label="Businessman in a suit walking beside a private jet" style="left:48px;top:336px;width:188px;height:126px;border-radius:0 50px 0 50px;background:linear-gradient(120deg,#c9d6df,#9a8a70 45%,#3a3228 80%)"></div>
    <p class="body" style="left:253px;top:347px;width:110px"><span style="font-size:7px">W</span>ith Velorane's fractional jet ownership program. You can enjoy the benefits of private jet travel without the hassle and expense of owning a whole aircraft. Our program offers flexibility, convenience, and access to a fleet of luxurious jets, allowing you to travel in style and comfort.</p>
    <div class="feature" style="top:394px"><span class="dot"></span>Flexible Ownership Options</div>
    <div class="feature" style="top:409px"><span class="dot"></span>Convenient Booking Process</div>
    <div class="feature" style="top:424px;border-bottom:none"><span class="dot"></span>Luxurious Fleet of Jets</div>
    <div class="btn outline" style="left:253px;top:442px;width:46px">Explore Now</div>
    <div class="learn" style="left:307px;top:447px">Learn More <i></i></div>
  </section>

  <section class="programs abs" style="left:23px;top:496px;width:361px;height:202px;background:var(--panel)">
    <div class="photo" role="img" aria-label="Woman in a leather jacket walking past private jets, black and white" style="left:198px;top:0;width:163px;height:202px;background:linear-gradient(160deg,#d0d0d0,#7b7b7b 45%,#2b2b2b)"></div>
  </section>
  <div class="eyebrow" style="left:48px;top:528px">Discover our programs</div>
  <div class="program active" style="top:540px"><h4>Flexible Ownership Options Available</h4><p>Choose from a variety of <b style="color:#fff">ownership programs</b> and enjoy the freedom to fly on your own terms.</p></div>
  <div class="program" style="top:585px"><h4>Convenient Jet Card Programs</h4><p>Choose from a variety of ownership programs and enjoy the freedom to fly on your own terms.</p></div>
  <div class="program" style="top:628px"><h4>Flexible Lease Programs</h4><p>Choose from a variety of ownership programs and enjoy the freedom to fly on your own terms.</p></div>

  <section class="experience">
    <div class="eyebrow" style="left:48px;top:738px">Get experience</div>
    <h2 class="h-section" style="left:48px;top:746px">Unparalleled Luxury &amp;<br>Convenience For <em>Private</em><br><em>Aviation</em></h2>
    <div class="photo" role="img" aria-label="Golden private jet inside a hangar" style="left:27px;top:847px;width:142px;height:119px;border-radius:0 0 0 60px;background:linear-gradient(140deg,#2a3440,#6b5a3a 50%,#c9a560 70%,#1a1a1a)"></div>
    <div class="photo" role="img" aria-label="Passenger working on a laptop by a cabin window" style="left:103px;top:797px;width:97px;height:89px;border-radius:0 45px 0 0;background:linear-gradient(135deg,#d5d5d5,#777 55%,#222)"></div>
    <div class="abs" style="left:71px;top:814px;width:29px;height:29px;border-radius:5px;background:linear-gradient(135deg,var(--gold-light),var(--gold))"></div>
    <p class="body" style="left:222px;top:811px;width:122px"><span style="font-size:7px">D</span>iscover the ultimate in luxury and convenience with Velorane. Our exclusive private aviations solutions provide you with unparalled access to the world of private jets, ensuring a seamless and extraordinary travel experience.</p>
    <div class="benefit" style="top:853px">
      <span class="tick"><svg width="9" height="7" viewBox="0 0 9 7"><path d="M1 3.5l2.5 2.5L8 1" fill="none" stroke="#d5b46a" stroke-width="1.4"/></svg></span>
      <div><h4>Convenience</h4><p>Choose from a variety of <b style="color:#fff">ownership programs</b> and<br>enjoy the freedom to fly on your own terms.</p></div>
    </div>
    <div class="benefit" style="top:898px">
      <span class="tick"><svg width="9" height="7" viewBox="0 0 9 7"><path d="M1 3.5l2.5 2.5L8 1" fill="none" stroke="#d5b46a" stroke-width="1.4"/></svg></span>
      <div><h4>Luxury</h4><p>Indulge in the lavish <b style="color:#fff">amenities and exquisite<br>interiors</b> of our private jets</p></div>
    </div>
    <div class="btn outline" style="left:222px;top:948px;width:46px">Explore Now</div>
    <div class="learn" style="left:276px;top:953px">Learn More <i></i></div>
  </section>

  <section class="why">
    <div class="eyebrow" style="left:0;width:408px;text-align:center;top:1023px">Why Velorane</div>
    <h2 class="h-section" style="left:0;width:408px;text-align:center;top:1031px">Experience The Ultimate in<br>Private <em>Jet Travel</em></h2>
    <p class="body" style="left:104px;width:200px;text-align:center;top:1065px;font-size:3px;line-height:6px">Velorane offers a wide range of exlusive services to meet your private jet travel needs. From fractional jet ownership to on-demand charter flights, we provide the highest level of luxury and convenience.</p>
    <div class="service" style="left:48px;top:1090px;height:70px">
      <svg width="16" height="16" viewBox="0 0 16 16"><path d="M2 9l12-5-3 8-3-3-6 0z" fill="#d5b46a"/></svg>
      <h4>On-Demand Charter</h4><div class="bar"></div><p>Fly anywhere, anytime with our on-</p>
    </div>
    <div class="service" style="left:155px;top:1090px;height:70px">
      <svg width="16" height="16" viewBox="0 0 16 16"><circle cx="8" cy="8" r="6.5" fill="none" stroke="#d5b46a" stroke-width="1.2"/><path d="M1.5 8h13M8 1.5c-3 3.5-3 9.5 0 13M8 1.5c3 3.5 3 9.5 0 13" fill="none" stroke="#d5b46a" stroke-width=".9"/></svg>
      <h4>Global Medical Response<br>And Recovery</h4><div class="bar" style="margin-top:3px"></div><p>We provide specialized medical transportation</p>
    </div>
    <div class="service" style="left:262px;top:1090px;height:70px">
      <svg width="16" height="16" viewBox="0 0 16 16"><circle cx="5" cy="6" r="3" fill="none" stroke="#d5b46a" stroke-width="1.3"/><path d="M7.5 7.5l6 0M11 7.5v3M13.5 7.5v2" stroke="#d5b46a" stroke-width="1.3" fill="none"/></svg>
      <h4>Fractional Jet Ownership</h4><div class="bar"></div><p>Enjoy the benefits of owning a private</p>
    </div>
  </section>
</main>

<!-- ===== Home page: lower half ===== -->
<main class="page right">
  <div class="service" style="left:48px;top:-10px;height:42px;padding-top:0">
    <div class="bar" style="margin-top:16px"></div><p>Fly anywhere, anytime with our on-<br>demand charter service.</p>
  </div>
  <div class="service" style="left:155px;top:-10px;height:42px;padding-top:0">
    <h4 style="margin-top:10px">And Recovery</h4><div class="bar" style="margin:2px 0 3px"></div><p>We provide specialized medical transportation services worldwide.</p>
  </div>
  <div class="service" style="left:262px;top:-10px;height:42px;padding-top:0">
    <div class="bar" style="margin-top:16px"></div><p>Enjoy the benefits of owning a private<br>jet without the hassles.</p>
  </div>
  <div class="btn outline" style="left:163px;top:43px;width:46px">Explore Now</div>
  <div class="learn" style="left:217px;top:47px">Learn More <i></i></div>

  <section class="cta-banner">
    <div class="photo" role="img" aria-label="Traveller walking toward a private jet on a wet runway at sunset" style="left:23px;top:88px;width:362px;height:128px;border-radius:30px 0 30px 0;background:linear-gradient(100deg,#15181c 0%,#1f2328 30%,#6b5434 60%,#c9a060 78%,#2b2a2a 100%)"></div>
    <h2 class="h-cta" style="left:47px;top:115px">Experience<br>Luxury Travel Like<em>Never Before</em></h2>
    <p class="body" style="left:48px;top:166px;font-size:3.5px">Contact Us today to book your exclusive Jet Experience</p>
    <div class="btn outline" style="left:48px;top:180px;width:46px">Explore Now</div>
    <div class="learn" style="left:102px;top:184px">Learn More <i></i></div>
  </section>

  <section class="testimonials">
    <div class="watermark" style="left:60px;top:244px;font-size:60px;color:rgba(255,255,255,.05)">TESTIMON</div>
    <div class="eyebrow" style="left:48px;top:246px">Testimonials</div>
    <h2 class="h-section" style="left:48px;top:254px">Trusted by worlds leading<br><em>Platforms</em></h2>

    <div class="testimonial" style="left:-71px;top:310px;opacity:.45"><div class="quote">“</div><div class="stars">★★★★★</div><p>Velorane's services have exceeded my expectations. The convenience and luxury of flying with them is unmatched.</p></div>
    <div class="brand abs" style="left:9px;top:384px;opacity:.6"><span class="sq"></span>Weblane</div>

    <div class="testimonial" style="left:79px;top:297px"><div class="quote">“</div><div class="stars">★★★★★</div><p>Velorane's services have exceeded my expectations. The convenience and luxury of flying with them is unmatched.</p></div>
    <div class="author" style="left:87px;top:366px"><span class="avatar"></span><span>ADRIAN COLE<small>CEO, HALVERN CORP</small></span></div>
    <div class="brand abs" style="left:161px;top:371px"><span class="sq"></span>Weblane</div>

    <div class="testimonial" style="left:209px;top:310px"><div class="quote">“</div><div class="stars">★★★★★</div><p>Velorane's services have exceeded my expectations. The convenience and luxury of flying with them is unmatched.</p></div>
    <div class="author" style="left:217px;top:379px"><span class="avatar"></span><span>ADRIAN COLE<small>CEO, HALVERN CORP</small></span></div>
    <div class="brand abs" style="left:290px;top:384px"><span class="sq"></span>Weblane</div>

    <div class="testimonial" style="left:360px;top:297px;opacity:.45"><div class="quote">“</div><div class="stars">★★★★★</div><p>Velorane's services have exceeded my expectations. The convenience and luxury of flying with them is unmatched.</p></div>
    <div class="author" style="left:368px;top:366px;opacity:.7"><span class="avatar"></span><span>ADRIAN COLE<small>CEO, HALVERN CORP</small></span></div>
  </section>

  <div class="rule" style="left:48px;top:419px;width:312px"></div>

  <section class="partners">
    <div class="eyebrow" style="left:0;width:408px;text-align:center;top:442px;font-size:3.4px;font-weight:600">Trusted by top-tier companies around the globe</div>
    <div class="abs" style="left:0;width:408px;top:459px;display:flex;justify-content:center;gap:8px">
      <span class="brand"><span class="sq"></span>Weblane</span><span class="brand"><span class="ci"></span>Frandle</span>
      <span class="brand"><span class="sq"></span>Weblane</span><span class="brand"><span class="ci"></span>Frandle</span>
      <span class="brand"><span class="sq"></span>Weblane</span><span class="brand"><span class="ci"></span>Frandle</span>
      <span class="brand"><span class="sq"></span>Weblane</span>
    </div>
    <div class="abs" style="left:0;width:408px;top:474px;display:flex;justify-content:center;gap:8px">
      <span class="brand"><span class="ci"></span>Frandle</span><span class="brand"><span class="sq"></span>Weblane</span>
      <span class="brand"><span class="ci"></span>Frandle</span><span class="brand"><span class="sq"></span>Weblane</span>
    </div>
  </section>

  <section class="newsletter abs" style="left:23px;top:506px;width:362px;height:127px;border-radius:30px 0 30px 0;overflow:hidden;background:linear-gradient(120deg,#f5e6a8 0%,#d8ba6c 40%,#a8843c 75%,#6e5424 100%)">
    <div class="photo" role="img" aria-label="Woman in sunglasses standing in front of a private jet" style="left:197px;top:0;width:165px;height:127px;background:linear-gradient(160deg,#dfe6ec,#a8a49a 45%,#6b5a44 80%)"></div>
  </section>
  <h2 class="h-cta" style="left:48px;top:529px;color:#111;line-height:17px">Subscribe To<em style="font-size:17px">Newsletter</em></h2>
  <p class="body" style="left:48px;top:565px;color:#222;font-size:3.4px">Stay updated with exclusive offers and industry news</p>
  <div class="abs" style="left:48px;top:577px;width:116px;height:14px;background:#fff;border-radius:2px;font-size:2.8px;color:#666;padding:5px 8px">your email address</div>
  <div class="btn dark" style="left:48px;top:596px;width:46px">Join Now</div>

  <section class="faq">
    <div class="watermark" style="left:48px;top:644px;font-size:50px;color:rgba(255,255,255,.05)">QUESTION</div>
    <div class="eyebrow" style="left:48px;top:671px">FAQ's</div>
    <h2 class="h-section" style="left:47px;top:679px">Frequently <em>Question</em></h2>
    <div class="rule" style="left:48px;top:717px;width:312px"></div>
    <div class="faq-q" style="top:726px;left:49px"><span>What Is Velorane ?</span><span>+</span></div>
    <div class="rule" style="left:48px;top:739px;width:312px"></div>
    <div class="faq-q" style="top:747px"><span>How It Works ?</span><span>−</span></div>
    <p class="body" style="left:48px;top:759px;width:300px;font-size:3px;line-height:6.6px">Velorane works by allowing customers to purchase fractional ownership of private jet, join jet card programs for a set number of flihts hours lease a private jet for a specific period, or access our all access and helicopter programs. we alos offer charter flights where customers can book individual seats on private jets.</p>
    <div class="rule" style="left:48px;top:788px;width:312px"></div>
    <div class="faq-q" style="top:796px"><span>Why Choose Velorane ?</span><span>+</span></div>
    <div class="rule" style="left:48px;top:810px;width:312px"></div>
    <div class="faq-q" style="top:818px"><span>How To Book ?</span><span>+</span></div>
    <div class="rule" style="left:48px;top:831px;width:312px"></div>
    <div class="faq-q" style="top:839px"><span>What Are The Benefits ?</span><span>+</span></div>
    <div class="rule" style="left:48px;top:853px;width:312px"></div>

    <h3 class="abs" style="left:48px;top:874px;font-size:7px;font-weight:500">Still Have Questions ?</h3>
    <p class="body" style="left:48px;top:883px;font-size:3px">Contact Us for more information.</p>
    <div class="btn outline" style="left:309px;top:876px;width:50px">Contact Us</div>
  </section>

  <section class="cta-final">
    <div class="photo" role="img" aria-label="Private jet flying over city lights at night" style="left:23px;top:923px;width:362px;height:127px;border-radius:30px 0 30px 0;background:radial-gradient(ellipse at 40% 90%,#6a5330 0%,#2a2620 35%,#14181d 70%,#0f1216 100%)"></div>
    <h2 class="h-cta" style="left:47px;top:950px">Experience<br>Luxury Travel Like<em>Never Before</em></h2>
    <p class="body" style="left:217px;top:955px;width:142px;font-size:3.2px;line-height:7px">Discover the ultimate in private jet travel with Velorane. Whether you're looking for fractional jet ownership, jet card programs, private jet lease programs, all access programs, helicopter access programs, or by the seat charter flights, we have perfect solution for your travel needs.</p>
    <div class="btn dark" style="left:217px;top:995px;width:42px;background:#0b0b0b">Book Now</div>
    <div class="btn outline" style="left:268px;top:995px;width:46px">Contact Us</div>
  </section>

  <footer>
    <div class="abs" style="left:-30px;top:1050px;width:180px;height:140px;border-radius:0 70px 0 0;background:#111"></div>
    <div class="logo abs" style="left:23px;top:1076px;font-size:12px"><span>Velorane</span><span class="mark"></span></div>
    <div class="foot-col" style="left:114px"><h5>About Us</h5><a>Charter</a><a>Fleet</a><a>Destinations</a><a>Pricing</a><a>Contact</a></div>
    <div class="foot-col" style="left:169px"><h5>Services</h5><a>Private Jets</a><a>Helicopters</a><a>Jet Cards</a><a>Membership</a><a>FAQ</a></div>
    <div class="foot-col" style="left:223px"><h5>Term</h5><a>Privacy</a><a>Careers</a><a>Press</a><a>Blog</a><a>Support</a></div>
    <div class="foot-col" style="left:269px"><h5>Subscribe</h5><a>Join our mailing list for the latest updates.</a></div>
    <div class="abs" style="left:269px;top:1101px;width:83px;height:12px;border:.5px solid #333;background:#141414;font-size:2.8px;color:#aaa;padding:4px 7px">Your Email Address</div>
    <div class="btn gold" style="left:353px;top:1101px;width:31px;height:12px;border-radius:2px">Sign Up</div>
    <p class="body" style="left:269px;top:1117px;width:80px;font-size:2.6px;line-height:4.4px;color:#aaa">by Subscribing, you agree to our privacy and consent to receive udates.</p>
    <div class="rule" style="left:23px;top:1150px;width:362px"></div>
    <p class="body" style="left:23px;top:1161px;font-size:2.8px">© 2024 Velorane. All rights reserved.</p>
    <p class="body" style="left:155px;top:1161px;font-size:2.8px">Privacy Policy</p>
    <p class="body" style="left:187px;top:1161px;font-size:2.8px">Terms Of service</p>
    <p class="body" style="left:225px;top:1161px;font-size:2.8px">Cookie Settings</p>
    <div class="social" style="left:332px"><i></i></div>
    <div class="social" style="left:344px"><i></i></div>
    <div class="social" style="left:356px"><i></i></div>
    <div class="social" style="left:368px"><i></i></div>
    <div class="social" style="left:380px"><i></i></div>
  </footer>
</main>

</body>
</html>
```